Business Cards for IT Consulting Company (Managed Service Provider)

I am looking to have some business cards printed and would like some designs. We are an IT Consulting company based in Vancouver BC. I would like a nice clean and modern look to the cards. I have uploaded all the versions of my logo so parts can be used as needed. Here is a snippit from our website homepage:

Quillbrook Networks Ltd. is an IT Solutions Partner located in Vancouver BC, Canada. We offer IT solutions and support to customers in the greater Vancouver Area. With expertise in Microsoft platforms, as well as Linux and Mac OSX and over 12 years experience in the IT industry, Quillbrook Networks is dedicated to offering our clients top quality service and products. We take pride in the solutions we offer our customers. The greatest compliment a client can give us is to recommend our services.

Quillbrook Networks Ltd. offers a wide range of IT services from onsite service to remote support and managed service solutions. This allows clients to choose the support path that best suits their company’s needs. Supporting many different sized companies from small to enterprise level over the past 12 years Quillbrook Networks has the experience and expertise needed to ensure things run smoothly. Allowing our clients to focus on doing business.

Revolutionizing the way IT services are delivered.

Quillbrook Networks is dedicated to providing our clients with IT solutions that work and grow with them for years to come. This philosophy helps save money in the long run instead of replacing equipment constantly. Far too often IT solutions are not well thought out and while possibly solving the problem at hand, require replacement due to growth or quality within a very short time frame. Quillbrook Networks takes pride in providing solutions that will last and be able to accommodate growth without the need for replacement.

Industry/Entity Type

Information Technology

Contact Information for Business Card

Quillbrook Networks Ltd.
(Employee Name)
Eml: (Employees Email Address)
Web: quillbrook.me
Ph: 604-555-0148

Font styles to use
Serif
Sans Serif

Requirements
Must have
• The Company logo and company colors.
Nice to have
• - Our tag line: "Revolutionizing IT Services" or "Revolutionizing the way IT services are delivered."
• - Also I really like the idea of nature and technology together blending which is sort of where my logo came from so integrating that somehow onto the business cards would be great.

```html
<!DOCTYPE html>
<html lang="en">
<head>
<meta charset="utf-8">
<title>Quillbrook Networks – Business Cards</title>
<link rel="stylesheet" href="https://fonts.googleapis.com/css2?family=Source+Sans+3:ital,wght@0,400;0,600;1,600&display=swap">
<style>
  :root {
    --backdrop: #000000;
    --card: #333437;
    --brand-blue: #1fa3dd;
    --text-light: #f2f2f2;
    --divider: #46474b;
  }
  * { margin: 0; padding: 0; box-sizing: border-box; }
  html, body {
    width: 1200px; height: 900px; overflow: hidden;
    background: var(--backdrop);
    font-family: "Source Sans 3", "Myriad Pro", sans-serif;
  }
  .stage { position: relative; width: 1200px; height: 900px; }
  .card {
    position: absolute; top: 271px;
    width: 457px; height: 281px;
    background: var(--card);
    border-radius: 14px;
    overflow: hidden;
  }
  .card--front { left: 137px; }
  .card--back { left: 626px; }

  .front-brand {
    position: absolute; left: 40px; top: 70px;
    width: 160px; height: 120px;
    display: flex; align-items: center; justify-content: center;
    color: var(--brand-blue);
    font-weight: 600; font-size: 26px; letter-spacing: 0.2px;
  }
  .front-divider {
    position: absolute; left: 214px; top: 68px;
    width: 1px; height: 122px; background: var(--divider);
  }
  .holder-name {
    position: absolute; left: 252px; top: 78px;
    color: var(--brand-blue); font-weight: 600; font-size: 17px;
  }
  .contact-list {
    position: absolute; left: 252px; top: 123px;
    list-style: none;
  }
  .contact-list li {
    display: flex; align-items: center; gap: 5px;
    height: 19px;
    color: var(--text-light); font-size: 13.5px;
  }
  .contact-list svg { width: 9px; height: 9px; fill: var(--brand-blue); flex: none; }

  .tagline-row {
    position: absolute; left: 0; right: 0; top: 222px;
    display: flex; align-items: center; gap: 10px;
  }
  .tagline-rule { height: 1px; background: var(--brand-blue); }
  .tagline-rule--left { width: 121px; }
  .tagline-rule--right { flex: 1; }
  .tagline {
    color: var(--brand-blue); font-style: italic; font-weight: 600; font-size: 15.5px;
    white-space: nowrap;
  }

  .back-brand {
    position: absolute; inset: 0;
    display: flex; align-items: center; justify-content: center;
    color: var(--brand-blue); font-weight: 600; font-size: 24px;
    padding-bottom: 10px;
  }
</style>
</head>
<body>
<main class="stage">
  <section class="card card--front" aria-label="Business card front">
    <div class="front-brand">Quillbrook</div>
    <div class="front-divider"></div>
    <h1 class="holder-name">Daniel Hartley</h1>
    <ul class="contact-list">
      <li>
        <svg viewBox="0 0 10 10" aria-hidden="true"><path d="M2 0.5 L3.6 2.6 L2.7 3.6 Q4 6 6.4 7.3 L7.4 6.4 L9.5 8 L8.4 9.5 Q4.5 9.3 2.2 6.8 Q0.5 4.5 0.5 1.6 Z"/></svg>
        <span>604-555-0148</span>
      </li>
      <li>
        <svg viewBox="0 0 10 10" aria-hidden="true"><path d="M0.5 2 H9.5 V8.5 H0.5 Z M0.5 2 L5 5.6 L9.5 2" stroke="#333437" stroke-width="0.8"/></svg>
        <span>info@quillbrook.me</span>
      </li>
      <li>
        <svg viewBox="0 0 10 10" aria-hidden="true"><circle cx="5" cy="5" r="4.6"/><path d="M0.6 5 H9.4 M5 0.4 Q2.6 5 5 9.6 Q7.4 5 5 0.4" stroke="#333437" stroke-width="0.6" fill="none"/></svg>
        <span>www.quillbrook.me</span>
      </li>
    </ul>
    <div class="tagline-row">
      <span class="tagline-rule tagline-rule--left"></span>
      <span class="tagline">Revolutionizing IT Services</span>
      <span class="tagline-rule tagline-rule--right"></span>
    </div>
  </section>

  <section class="card card--back" aria-label="Business card back">
    <div class="back-brand">Quillbrook Networks Ltd.</div>
  </section>
</main>
</body>
</html>
```